Brightmill Data Works

Our company is about IT hardwares and IT solutions. IT hardware such as PC, RAMS, storage and servers. IT solutions such as project management, BA. We are also selling new technology too.

Target Market(s)

Consumer, Small to Medium Business, Corporate

Requirements
Must have
• The business card must have the following:
• Name:
• Title:
• Contact Number:
• Email address:
• Website:
• Color: Must match the logo color upgrade

```html
<!DOCTYPE html>
<html lang="en">
<head>
<meta charset="UTF-8">
<title>Brightmill Data Works — Business Card</title>
<link rel="stylesheet" href="https://fonts.googleapis.com/css2?family=Work+Sans:wght@400;500;700;800&display=swap">
<style>
  :root {
    --backdrop: #161616;
    --card: #242424;
    --card-deep: #1c1c1c;
    --pattern-tone: #3a3a3a;
    --accent: #e08a2c;
    --accent-deep: #c96a1f;
    --ink-light: #f2f2f2;
    --ink-soft: #d8d8d8;
  }
  * { margin: 0; padding: 0; box-sizing: border-box; }
  html, body {
    width: 1200px; height: 900px; overflow: hidden;
    background: var(--backdrop);
    font-family: "Work Sans", sans-serif;
  }
  .stage { position: relative; width: 1200px; height: 900px; }
  .card {
    position: absolute; left: 250px; width: 700px; height: 390px;
    border-radius: 4px;
    box-shadow: 0 14px 30px rgba(0,0,0,.55);
    overflow: hidden;
  }
  .card-back {
    top: 45px;
    background: linear-gradient(120deg, var(--card-deep) 0%, #262626 55%, #2e2e2e 100%);
  }
  .pattern-field {
    position: absolute; inset: 0;
    background:
      radial-gradient(ellipse at 70% 40%, rgba(255,255,255,.10), transparent 55%),
      linear-gradient(120deg, transparent 0%, rgba(90,90,90,.18) 60%, rgba(120,120,120,.22) 100%);
  }
  .back-accent {
    position: absolute; left: 470px; top: 258px;
    display: flex; align-items: center; gap: 10px;
  }
  .back-accent-dot {
    width: 30px; height: 30px; border-radius: 50%;
    background: linear-gradient(135deg, var(--accent), var(--accent-deep));
  }
  .back-accent-name {
    color: var(--accent); font-weight: 800; font-size: 16px;
    text-transform: uppercase; letter-spacing: .5px;
  }
  .card-front {
    top: 465px;
    background: linear-gradient(135deg, var(--card-deep) 0%, var(--card) 55%, #2c2c2c 100%);
  }
  .brand {
    position: absolute; left: 30px; top: 0; width: 320px; height: 390px;
    display: flex; flex-direction: column; align-items: center; justify-content: center;
    gap: 20px;
  }
  .brand-dot {
    width: 56px; height: 56px; border-radius: 50%;
    background: linear-gradient(135deg, var(--accent), var(--accent-deep));
  }
  .brand-name {
    color: var(--ink-light); font-weight: 800; font-size: 36px;
    text-transform: uppercase; letter-spacing: .5px; text-align: center; line-height: 1.1;
  }
  .divider {
    position: absolute; left: 372px; top: 90px; width: 2px; height: 210px;
    background: var(--ink-light);
  }
  .details {
    position: absolute; left: 400px; top: 90px; width: 290px;
    color: var(--ink-light);
  }
  .person-name {
    color: var(--accent); font-weight: 500; font-size: 28px;
    text-transform: uppercase; line-height: 1;
  }
  .person-title { font-size: 17px; margin-top: 4px; }
  .address { font-size: 16px; line-height: 1.4; margin-top: 16px; color: var(--ink-soft); }
  .contact-list { list-style: none; margin-top: 14px; }
  .contact-list li {
    display: flex; align-items: center; gap: 10px;
    font-size: 17px; line-height: 1.5;
  }
  .contact-list svg { width: 14px; height: 14px; flex: none; }
  .domain { color: var(--accent); }
</style>
</head>
<body>
<main class="stage">
  <section class="card card-back">
    <div class="pattern-field" role="img" aria-label="Repeating tonal brand-mark pattern across the dark card back"></div>
    <div class="back-accent">
      <span class="back-accent-dot"></span>
      <span class="back-accent-name">Brightmill Data Works</span>
    </div>
  </section>

  <section class="card card-front">
    <div class="brand">
      <span class="brand-dot"></span>
      <h1 class="brand-name">Brightmill<br>Data Works</h1>
    </div>
    <div class="divider"></div>
    <div class="details">
      <h2 class="person-name">Daniel Rourke</h2>
      <p class="person-title">Director</p>
      <p class="address">2250 Orchard Mill Rd<br>Alder, CA 95410-3318</p>
      <ul class="contact-list">
        <li>
          <svg viewBox="0 0 16 16" aria-hidden="true"><path d="M4 1.5 6 5 4.6 6.4c.8 2 2.4 3.6 4.4 4.4L10.5 9.5 14 11.5 13 14C7 14 2 9 2 3z" fill="none" stroke="var(--accent)" stroke-width="1.5" stroke-linejoin="round"/></svg>
          555-204-7731
        </li>
        <li>
          <svg viewBox="0 0 16 16" aria-hidden="true"><rect x="1.5" y="3.5" width="13" height="9" fill="none" stroke="var(--accent)" stroke-width="1.5"/><path d="M1.5 3.5 8 9l6.5-5.5" fill="none" stroke="var(--accent)" stroke-width="1.5"/></svg>
          info@brightmilldata.com
        </li>
        <li>
          <svg viewBox="0 0 16 16" aria-hidden="true"><g fill="none" stroke="var(--accent)" stroke-width="1.3"><circle cx="8" cy="8" r="6.5"/><ellipse cx="8" cy="8" rx="3" ry="6.5"/><path d="M1.5 8h13"/></g></svg>
          <span>www.<span class="domain">brightmilldata</span>.com</span>
        </li>
      </ul>
    </div>
  </section>
</main>
</body>
</html>
```